Modern HomePage Design for Church

We are looking for a modern homepage design using the sections we put together in the template. The colors we want are blue, black, grey, and white. We do not want use the colors in the logo. Please modify the logo color to match the website color scheme.

Target Market(s)

Church

Industry/Entity Type

Church

Number of Pages Required

1 page

Colors
0293ce
ffffff
474747
9d9d9d

```html
<!DOCTYPE html>
<html lang="en">
<head>
<meta charset="utf-8">
<title>Wellspring Community Church</title>
<link href="https://fonts.googleapis.com/css2?family=Poppins:wght@500;600;700&family=Open+Sans:wght@400;600;700&display=swap" rel="stylesheet">
<style>
:root{
  --blue:#0293ce;
  --white:#ffffff;
  --ink:#474747;
  --grey:#9d9d9d;
  --light:#f3f1f1;
  --dark:#2b2b2b;
  --darker:#1e1e1e;
  --text:#555555;
}
*{box-sizing:border-box;margin:0;padding:0}
html,body{width:1200px;height:4932px;overflow:hidden}
body{font-family:"Open Sans",sans-serif;color:var(--text);background:var(--white);position:relative}
.h{font-family:"Poppins",sans-serif;font-weight:700;text-transform:uppercase}
.abs{position:absolute}
.btn{position:absolute;background:var(--blue);color:var(--white);font-family:"Open Sans",sans-serif;font-weight:700;font-size:13px;display:flex;align-items:center;justify-content:center;text-transform:uppercase;letter-spacing:.5px}
.photo{position:absolute}
p{font-size:15px;line-height:1.6}

/* header */
.site-header{position:absolute;top:0;left:0;width:1200px;height:132px;background:var(--white)}
.brand{position:absolute;left:130px;top:26px;display:flex;align-items:center;gap:12px}
.brand-dot{width:34px;height:34px;border-radius:50%;background:var(--blue)}
.brand-name{font-family:"Poppins",sans-serif;font-weight:600;color:var(--blue);font-size:22px;line-height:1.05;text-transform:uppercase}
.top-btn{position:absolute;top:30px;height:33px;background:var(--ink);color:var(--white);font-size:11px;font-weight:600;display:flex;align-items:center;justify-content:center}
.give-btn{position:absolute;top:26px;left:927px;width:141px;height:41px;background:var(--blue);color:var(--white);font-weight:700;font-size:15px;display:flex;align-items:center;justify-content:center}
.main-nav{position:absolute;top:90px;left:454px;width:616px;display:flex;justify-content:space-between;font-size:14px;font-weight:600;color:var(--ink);text-transform:uppercase}
.main-nav .active{color:var(--blue)}

/* hero */
.hero{position:absolute;top:132px;left:0;width:1200px;height:568px;background:linear-gradient(180deg,#1d2a3a 0%,#34414f 40%,#7a4a1c 70%,#c46b18 85%,#2a1a0e 100%)}
.hero-title{position:absolute;top:150px;width:100%;text-align:center;color:var(--white);font-size:48px}
.hero-sub{position:absolute;top:222px;width:100%;text-align:center;color:var(--white);font-weight:700;font-size:22px}
.dots{position:absolute;top:515px;left:0;width:100%;display:flex;justify-content:center;gap:12px}
.dots span{width:9px;height:9px;border-radius:50%;background:rgba(255,255,255,.6)}
.dots span.on{background:var(--white)}

/* visitor band */
.visitor{position:absolute;top:700px;left:0;width:1200px;height:100px;background:var(--blue)}
.visitor-text{position:absolute;left:142px;top:38px;color:var(--white);font-weight:700;font-size:16px}
.visitor-btn{position:absolute;left:894px;top:32px;width:142px;height:38px;background:var(--dark);color:var(--white);font-weight:600;font-size:13px;display:flex;align-items:center;justify-content:center}

/* welcome */
.welcome{position:absolute;top:800px;left:0;width:1200px;height:508px;background:var(--light)}
.welcome-kicker{position:absolute;left:132px;top:72px;font-size:20px;color:var(--ink);font-weight:600}
.welcome-title{position:absolute;left:132px;top:106px;font-size:30px;line-height:1.3;color:var(--ink)}
.welcome-rule{position:absolute;left:132px;top:203px;width:453px;height:1px;background:var(--grey)}
.welcome-copy{position:absolute;left:132px;top:240px;width:455px;color:var(--text)}

/* meeting */
.meeting{position:absolute;top:1308px;left:0;width:1200px;height:264px;background:var(--dark)}
.meeting-title{position:absolute;left:138px;top:58px;color:var(--white);font-size:32px}
.meeting-date{position:absolute;left:138px;top:104px;color:var(--white);font-size:19px}
.meeting-copy{position:absolute;left:138px;top:160px;width:440px;color:#cfcfcf;font-size:14px}
.countdown{position:absolute;left:670px;top:66px;display:flex}
.count{width:104px;text-align:center;border-left:1px solid #555;color:var(--white)}
.count:first-child{border-left:none}
.count small{display:block;font-size:11px;color:#bbb;text-transform:uppercase}
.count b{display:block;font-family:"Poppins",sans-serif;font-size:32px;line-height:1.2}

/* features */
.features{position:absolute;top:1572px;left:0;width:1200px;height:473px;background:var(--white)}
.feature{position:absolute;top:60px;width:300px;text-align:center}
.feature svg{display:block;margin:0 auto}
.feature h3{font-size:17px;color:var(--ink);margin-top:36px}
.feature p{font-size:14px;margin-top:14px;color:var(--text)}

/* involved */
.involved{position:absolute;top:2045px;left:0;width:1200px;height:437px;background:var(--light)}
.involved h2{position:absolute;left:707px;width:493px;top:135px;text-align:center;font-size:34px;color:var(--ink)}
.involved p{position:absolute;left:795px;width:320px;top:200px;text-align:center;font-size:14px}

/* blog */
.blog{position:absolute;top:2482px;left:0;width:1200px;height:468px;background:var(--light)}
.blog-panel{position:absolute;left:0;top:0;width:602px;height:468px;background:var(--dark)}
.blog-panel h2{position:absolute;left:60px;top:68px;color:var(--white);font-size:32px}
.blog-post h3{position:absolute;left:300px;top:152px;width:260px;color:var(--white);font-size:17px;line-height:1.35}
.blog-post p{position:absolute;left:300px;top:222px;width:250px;color:#cfcfcf;font-size:14px;line-height:1.5}
.pray h2{position:absolute;left:694px;top:80px;font-size:32px;color:var(--ink)}
.pray p{position:absolute;left:694px;top:140px;width:420px;font-size:14px}

/* pastor */
.pastor{position:absolute;top:2950px;left:0;width:1200px;height:528px;background:radial-gradient(ellipse at 50% 60%,#3a3a3a 0%,#1f1f1f 60%,#141414 100%)}
.pastor .label{position:absolute;top:90px;color:var(--white);font-size:16px}
.quote{position:absolute;left:408px;top:160px;color:var(--white);font-size:26px;line-height:1.3;width:260px}
.quote-copy{position:absolute;left:408px;top:252px;width:270px;color:#d0d0d0;font-size:14px;line-height:1.45}
.podcast{position:absolute;left:783px;width:300px;display:flex;gap:25px}
.podcast .play{width:40px;height:40px;border:2px solid var(--white);flex:none;display:flex;align-items:center;justify-content:center}
.podcast b{display:block;color:var(--white);font-size:15px;line-height:1.35}
.podcast small{display:block;color:var(--white);font-size:11px;font-weight:700;margin-top:12px;text-transform:uppercase}

/* events */
.events{position:absolute;top:3478px;left:0;width:1200px;height:1036px;background:var(--light)}
.events h2{position:absolute;top:60px;width:100%;text-align:center;font-size:34px;color:var(--ink)}
.events .sub{position:absolute;top:112px;width:100%;text-align:center;font-size:15px}
.event{position:absolute;left:132px;width:936px;height:248px;background:var(--white)}
.event-date{position:absolute;left:-53px;top:0;width:46px;height:58px;background:var(--blue);color:var(--white);text-align:center;padding-top:6px}
.event-date b{display:block;font-size:20px;line-height:1}
.event-date small{font-size:9px}
.event h3{position:absolute;left:331px;top:34px;width:400px;font-size:20px;color:var(--ink);line-height:1.3}
.meta{position:absolute;left:331px;display:flex;align-items:center;gap:12px;font-size:14px}
.meta .ic{width:22px;height:22px;border-radius:50%;background:var(--blue);flex:none}
.meta.church{color:var(--blue);font-weight:700}

/* footer */
.site-footer{position:absolute;top:4514px;left:0;width:1200px;height:418px;background:var(--darker);color:var(--white)}
.site-footer h4{position:absolute;top:64px;font-size:14px;font-weight:700;text-transform:uppercase}
.foot-item{position:absolute;display:flex;gap:20px;width:320px}
.foot-item .thumb{width:75px;height:50px;flex:none;background:linear-gradient(135deg,#6b4a22,#c89a4a)}
.foot-item b{display:block;font-size:11px;text-transform:uppercase}
.foot-item span{display:block;font-size:11px;color:#c9c9c9;line-height:1.4}
.menu-list{position:absolute;left:533px;top:106px;list-style:none;font-size:12px;line-height:1.4;color:#d6d6d6}
.foot-rule{position:absolute;left:132px;top:326px;width:936px;height:1px;background:#3a3a3a}
.copyright{position:absolute;top:372px;width:100%;text-align:center;font-size:11px;color:#bdbdbd}
</style>
</head>
<body>

<header class="site-header">
  <div class="brand"><span class="brand-dot"></span><span class="brand-name">Wellspring<br>Community Church</span></div>
  <div class="top-btn" style="left:546px;width:171px">SUNDAY WORSHIP 10:15</div>
  <div class="top-btn" style="left:737px;width:170px">SUNDAY SCHOOL 09:00</div>
  <div class="give-btn">GIVE ONLINE</div>
  <nav class="main-nav"><span class="active">Home</span><span>Team</span><span>Features</span><span>Events</span><span>Sermons</span><span>Blog</span><span>Contacts</span></nav>
</header>

<section class="hero" role="img" aria-label="Cathedral lit at dusk against a cloudy evening sky">
  <h1 class="hero-title h">Wellspring Community Church</h1>
  <div class="hero-sub">Lorem Ipsum is simply dummy text of the printing</div>
  <div class="btn" style="left:520px;top:296px;width:160px;height:49px;font-size:15px">Read More</div>
  <div class="dots"><span class="on"></span><span></span><span></span><span></span><span></span></div>
</section>

<section class="visitor">
  <div class="visitor-text">First time Visitor?... Find out how, where and when we worship, We hope to see you soon!</div>
  <div class="visitor-btn">VISITORS INFO</div>
</section>

<section class="welcome">
  <div class="welcome-kicker">WELCOME TO</div>
  <h2 class="welcome-title h">Wellspring<br>Community Church</h2>
  <div class="welcome-rule"></div>
  <p class="welcome-copy">Lorem ipsum dolor sit amet, consectetur adipiscing elit, sed do eiusmod tempor incididunt ut labore et dolore magna aliqua. Ut enim ad minim veniam, quis nostrud exercitation ullamco laboris nisi ut aliquip ex ea commodo consequat. Duis aute irure dolor in reprehenderit in voluptate velit esse cillum dolore eu fugiat nulla pariatur. Excepteur sint occaecat cupidatat non proident, sunt in culpa qui officia deserunt mollit anim id est laborum.</p>
  <div class="photo" role="img" aria-label="Portrait of the lead pastor and his wife" style="left:625px;top:30px;width:460px;height:478px;background:linear-gradient(180deg,#e9e6e4 0%,#b9aaa0 45%,#2a2a2a 100%)"></div>
</section>

<section class="meeting">
  <h2 class="meeting-title h">Church Leaders Meeting</h2>
  <div class="meeting-date">March 27, 2019 7:00 PM</div>
  <p class="meeting-copy">Meeting for the church leaders, This is where we plan the strategy for the church and give feedback on projects.</p>
  <div class="countdown">
    <div class="count"><small>Days</small><b>06</b></div>
    <div class="count"><small>Hours</small><b>15</b></div>
    <div class="count"><small>Minutes</small><b>28</b></div>
    <div class="count"><small>Seconds</small><b>16</b></div>
  </div>
  <div class="btn" style="left:805px;top:162px;width:125px;height:40px">Read More</div>
</section>

<section class="features">
  <div class="feature" style="left:113px">
    <svg width="96" height="90" viewBox="0 0 96 90" fill="none" stroke="#0293ce" stroke-width="6" stroke-linejoin="round"><path d="M48 84 L10 46 C-2 32 6 8 26 8 C38 8 44 16 48 22 C52 16 58 8 70 8 C90 8 98 32 86 46 Z"/><path d="M12 46 H34 L40 34 L50 60 L58 40 L64 46 H86" stroke-width="5"/></svg>
    <h3 class="h">What we believe?</h3>
    <p>Lorem ipsum dolor sit amet, consectetur adipiscing elit, sed do eiusmod tempor incididunt ut labore et dolore magna aliqua.</p>
    <div class="btn" style="left:93px;top:292px;width:115px;height:37px">Read More</div>
  </div>
  <div class="feature" style="left:448px">
    <svg width="92" height="92" viewBox="0 0 92 92" fill="none" stroke="#0293ce" stroke-width="7"><circle cx="46" cy="46" r="40"/><path d="M46 20 V48 L62 58" stroke-linecap="round"/></svg>
    <h3 class="h">Services &amp; Location</h3>
    <p>Lorem ipsum dolor sit amet, consectetur adipiscing elit, sed do eiusmod tempor incididunt ut labore et dolore magna aliqua.</p>
    <div class="btn" style="left:93px;top:292px;width:115px;height:37px">Read More</div>
  </div>
  <div class="feature" style="left:784px">
    <svg width="92" height="92" viewBox="0 0 92 92"><circle cx="52" cy="24" r="20" fill="#0293ce"/><text x="52" y="32" text-anchor="middle" font-family="Poppins,sans-serif" font-weight="700" font-size="22" fill="#fff">$</text><path d="M6 62 H30 C38 62 44 66 48 70 H64 M30 76 H58 L82 60 C88 56 92 64 86 70 L66 86 H20" fill="none" stroke="#0293ce" stroke-width="6" stroke-linejoin="round" stroke-linecap="round"/></svg>
    <h3 class="h">Giving</h3>
    <p>Lorem ipsum dolor sit amet, consectetur adipiscing elit, sed do eiusmod tempor incididunt ut labore et dolore magna aliqua.</p>
    <div class="btn" style="left:93px;top:292px;width:115px;height:37px">Read More</div>
  </div>
</section>

<section class="involved">
  <div class="photo" role="img" aria-label="Group praying around a table" style="left:10px;top:13px;width:345px;height:203px;background:linear-gradient(135deg,#3b2a22,#7a5a48)"></div>
  <div class="photo" role="img" aria-label="Couple walking through a church hall" style="left:362px;top:13px;width:171px;height:203px;background:linear-gradient(135deg,#5c5c5c,#2c2c2c)"></div>
  <div class="photo" role="img" aria-label="Hands joined in prayer" style="left:540px;top:13px;width:167px;height:203px;background:linear-gradient(135deg,#6a6a6a,#262626)"></div>
  <div class="photo" role="img" aria-label="People kneeling in prayer" style="left:10px;top:223px;width:168px;height:204px;background:linear-gradient(135deg,#8a6a4a,#3a2a1a)"></div>
  <div class="photo" role="img" aria-label="Open Bible with hands resting on it" style="left:185px;top:223px;width:170px;height:204px;background:linear-gradient(135deg,#7a5a3a,#2e2218)"></div>
  <div class="photo" role="img" aria-label="Congregation seated in church" style="left:362px;top:223px;width:345px;height:204px;background:linear-gradient(135deg,#a0582a,#4a2a18)"></div>
  <h2 class="h">Get Involved</h2>
  <p>Lorem ipsum dolor sit amet, consectetur adipiscing elit, sed do eiusmod tempor incididunt ut labore et dolore magna aliqua.</p>
</section>

<section class="blog">
  <div class="blog-panel">
    <h2 class="h">Latest Blog</h2>
    <div class="photo" role="img" aria-label="Illuminated church interior with blue vaulted ceiling" style="left:60px;top:148px;width:197px;height:230px;background:linear-gradient(180deg,#2a3a7a,#6a3a5a 60%,#c8903a)"></div>
    <div class="blog-post">
      <h3 class="h">Lorem Ipsum is simply dummy text</h3>
      <p>Lorem ipsum dolor sit amet, consectetur adipiscing elit, sed do eiusmod tempor incididunt ut labore et dolore magna aliqua.</p>
      <div class="btn" style="left:300px;top:329px;width:112px;height:37px">Read More</div>
    </div>
  </div>
  <div class="pray">
    <h2 class="h">Pray Without Chasing</h2>
    <p>Lorem ipsum dolor sit amet, consectetur adipiscing elit, sed do eiusmod tempor incididunt ut labore et dolore magna aliqua. adipisci velit, sed quia non numquam eius modi tempora incidunt ut labore et dolore magnam aliquam quaerat voluptatem. Ut enim ad minima veniam, quis nostrum exercitationem ullam corporis suscipit laboriosam.</p>
    <div class="btn" style="left:694px;top:339px;width:125px;height:40px">Read More</div>
  </div>
</section>

<section class="pastor" role="img" aria-label="Crowd with raised hands at a worship gathering">
  <div class="label h" style="left:132px">Pastor</div>
  <div class="photo" role="img" aria-label="Twin-spired church under a blue sky with birds" style="left:132px;top:131px;width:233px;height:312px;background:linear-gradient(180deg,#4a7ac0 0%,#8ab0d8 50%,#a05a3a 100%)"></div>
  <div class="abs" style="left:390px;top:150px;color:#fff;font-size:40px;font-family:Poppins,sans-serif;line-height:1">&ldquo;</div>
  <div class="quote h">One thing I ask of the Lord &rdquo;</div>
  <p class="quote-copy">Lorem ipsum dolor sit amet, consectetur adipiscing elit, sed do eiusmod tempor incididunt ut labore et dolore magna aliqua. circumstances occur in which toil and pain can procure him some great pleasure. To take a trivial example, which of us ever undertakes laborious.</p>
  <div class="label h" style="left:783px">Podcasts</div>
  <div class="podcast" style="top:140px"><div class="play"><svg width="14" height="16"><path d="M1 1 L13 8 L1 15 Z" fill="#fff"/></svg></div><div><b>Lorem ipsum dolor sit amet, consectetur adipiscing elit</b><small>By Samuel</small></div></div>
  <div class="podcast" style="top:256px"><div class="play"><svg width="14" height="16"><path d="M1 1 L13 8 L1 15 Z" fill="#fff"/></svg></div><div><b>Lorem ipsum dolor sit amet, consectetur adipiscing elit</b><small>By Samuel</small></div></div>
  <div class="podcast" style="top:377px"><div class="play"><svg width="14" height="16"><path d="M1 1 L13 8 L1 15 Z" fill="#fff"/></svg></div><div><b>Lorem ipsum dolor sit amet, consectetur adipiscing elit</b><small>By Samuel</small></div></div>
</section>

<section class="events">
  <h2 class="h">Upcoming Events</h2>
  <div class="sub">Experience God's Presence</div>

  <article class="event" style="top:182px">
    <div class="event-date"><b>22</b><small>Feb,2019</small></div>
    <div class="photo" role="img" aria-label="Golden church altar interior" style="left:23px;top:20px;width:272px;height:208px;background:linear-gradient(180deg,#3a2a1a,#a8783a 60%,#5a3a1a)"></div>
    <h3 class="h">Lorem Ipsum is simply dummy text of the printing</h3>
    <div class="meta" style="top:118px"><span class="ic"></span>Thursday, 08:00 AM - Thursday, 09:00 AM</div>
    <div class="meta church" style="top:150px"><span class="ic"></span>St. Meadowbrook Church</div>
    <div class="meta" style="top:190px"><span class="ic"></span>Elm Row, Riverton, United States, 20417</div>
    <div class="btn" style="left:768px;top:102px;width:129px;height:40px">Read More</div>
  </article>

  <article class="event" style="top:451px">
    <div class="event-date"><b>22</b><small>Feb,2019</small></div>
    <div class="photo" role="img" aria-label="Black and white crowd with raised hands" style="left:23px;top:20px;width:272px;height:208px;background:linear-gradient(180deg,#8a8a8a,#1e1e1e)"></div>
    <h3 class="h">Lorem Ipsum is simply dummy text of the printing</h3>
    <div class="meta" style="top:118px"><span class="ic"></span>Thursday, 08:00 AM - Thursday, 09:00 AM</div>
    <div class="meta church" style="top:150px"><span class="ic"></span>St. Meadowbrook Church</div>
    <div class="meta" style="top:190px"><span class="ic"></span>Elm Row, Riverton, United States, 20417</div>
    <div class="btn" style="left:768px;top:102px;width:129px;height:40px">Read More</div>
  </article>

  <article class="event" style="top:724px">
    <div class="event-date"><b>22</b><small>Feb,2019</small></div>
    <div class="photo" role="img" aria-label="Hands holding a worn leather Bible" style="left:23px;top:20px;width:272px;height:208px;background:linear-gradient(135deg,#d8c8b8,#5a3a22 60%,#2a1a10)"></div>
    <h3 class="h">Lorem Ipsum is simply dummy text of the printing</h3>
    <div class="meta" style="top:118px"><span class="ic"></span>Thursday, 08:00 AM - Thursday, 09:00 AM</div>
    <div class="meta church" style="top:150px"><span class="ic"></span>St. Meadowbrook Church</div>
    <div class="meta" style="top:190px"><span class="ic"></span>Elm Row, Riverton, United States, 20417</div>
    <div class="btn" style="left:768px;top:102px;width:129px;height:40px">Read More</div>
  </article>
</section>

<footer class="site-footer">
  <h4 style="left:132px">Latest Sermons</h4>
  <div class="foot-item" style="left:132px;top:110px"><div class="thumb" role="img" aria-label="Sermon thumbnail"></div><div><b>Lorem Ipsum is simply dummy</b><span>Lorem Ipsum is simply dummy text of the printing and typesetting industry.</span></div></div>
  <div class="foot-item" style="left:132px;top:202px"><div class="thumb" role="img" aria-label="Sermon thumbnail"></div><div><b>Lorem Ipsum is simply dummy</b><span>Lorem Ipsum is simply dummy text of the printing and typesetting industry.</span></div></div>
  <h4 style="left:533px">Menus</h4>
  <ul class="menu-list"><li>Home</li><li>Team</li><li>Features</li><li>Events</li><li>Sermons</li><li>Blog</li><li>Contact Us</li></ul>
  <h4 style="left:750px">Latest News</h4>
  <div class="foot-item" style="left:750px;top:110px"><div class="thumb" role="img" aria-label="News thumbnail"></div><div><b>Lorem Ipsum is simply dummy</b><span>Lorem Ipsum is simply dummy text of the printing and typesetting industry.</span></div></div>
  <div class="foot-item" style="left:750px;top:202px"><div class="thumb" role="img" aria-label="News thumbnail"></div><div><b>Lorem Ipsum is simply dummy</b><span>Lorem Ipsum is simply dummy text of the printing and typesetting industry.</span></div></div>
  <div class="foot-rule"></div>
  <div class="copyright">Copyright &copy; 2019 All Rights Reserved</div>
</footer>

</body>
</html>
```